Hurricane Damage Public Adjuster Billboard

I have created several projects with you and have several great designs. I need to format them into a Billboard for upcoming Hurricane Season. Need done in a month. Im also in process of getting an eye catching and easy to remember 800# Vanity phone number like Call 800-Stormsafe or 800- Need Fix? My included past Craft Huddle projects will give you an idea of what colors, schemes, and designs I gravitate towards. 3 past Design projects were 1) 2 Logos where I picked the 1st place and the 2nd place and 2) Index Card where I picked the winner as the Index Card and the 2nd place as a Post Card. Point is, I will pick and pay for 2 winners if they're good. This should help to sweeten the pot. Also, please look at my website for ideas that I like:

www.TheClaimKeeperGroup.com
I want people to feel that I am the best and highest. Level.

I've been getting a lot of quick half effort designs basically cut & pasting my previous projects. Please don't rush and take your time to be creative. A an example, my Biggest Competitor is Vesta Public Adjusting. Their colors are Black and Gold while mine are Blue, White, and Black with a highlight of Orange if possible. I JUST imported a picture of their BillBoard. I need mine better and BLOW AWAY THEIRS. Terms like "Don't be Victimized Twice ?, Don't let the Hurricane Ruin your Life?". "Get Fairly Paid & Move On" "Our Clients Claims are VIP?
Updates

I'm getting a lot of quick half effort ones. I'd rather you take your time and really put some thoughts and effort into it. My Biggest Competitor is Vesta Public Adjusting. They have black & gold colors, while I have Blue, Black, and white.

It needs to blow theirs away. I have imported their Billboard for comparative purposes.

Guy's,
I'll make it easier for you in what I'm looking for. Please look at the Vesta Billboard picture attached.

1) Put my "Blue Shield" to the left, replacing their logo
2) change color patterns from their (Black, Gold, White) to my color schemes of (Black, Blue, White)
3) I want to see my name where their is:

THE
Claim Keeper's Group
EXPERT & LOCAL Public Adjusters
"FOR THE POLICYHOLDER!!"

4) to the right, add the A+Rated logo and QRS+ Accredited logo, 5 Star Zorbix Rated logo, 5 Start PORCHLINE Highly Rated logo, etc..

5) the right side is where you can be creative as I will not have a picture of me there.

"20+ Years of Experience, Recovering Millions for our VIP Clients"

"Your Best, Locally-Based Private Adjuster & Advocate'
"FOR THE POLICYHOLDER!!"

"Don't be victimized Twice!!"

"Don't let the Hurricane Ruin Your Life!!"

This should really help. Also, refer to my website, maybe a couple testimonial fillers?

Thanks all,

marcus@TheClaimKeeperGroup.com

Just imported a few awards that would look great to the right side with all the other 5 Star Ratings and accolades.
This right section could be titled like zmy Website:

5 Star Reviews, Ratings & Awards:
4-5 Logos underneath?

Target Market(s)

Coastal place where a Hurricane 🌀 🌀 Hits

Industry/Entity Type

Hurricane Public Insurance Adjuster

Font styles to use
Sans Serif
Other font styles liked:
• Zurich fonts

Colors
0054AA
0677BA
7BADD7
CADEEF
E8F1F8
EE7325
F08F49
F5BC92
FAE3D3
FDF4ED

Requirements
Must have
• Use my past project logos, colors, and schemes to create eye grabbing BillBoard
Nice to have
Should not have
• Not be too busy, must be Easy to Read, Eye Catchy

```html
<!DOCTYPE html>
<html lang="en">
<head>
<meta charset="utf-8">
<title>The Claim Keeper's Group – Billboard</title>
<link rel="stylesheet" href="https://fonts.googleapis.com/css2?family=Cinzel:wght@500;700&family=Playfair+Display:ital,wght@1,900&family=Poppins:wght@600;700&display=swap">
<style>
  :root {
    --page: #d3d8dd;
    --ink: #1b1b1b;
    --white: #ffffff;
    --blue: #00a3df;
    --badge-blue: #0b5f99;
    --orange: #d98a35;
    --red: #e6202a;
    --green: #7ed321;
    --star: #f5a623;
  }
  * { margin: 0; padding: 0; box-sizing: border-box; }
  html, body {
    width: 1190px; height: 1200px; overflow: hidden;
    background: var(--page);
  }
  .billboard {
    position: absolute; left: 40px; top: 432px;
    width: 1110px; height: 337px;
    background: var(--white);
    box-shadow: 0 14px 24px rgba(0,0,0,0.22);
    font-family: "Poppins", sans-serif;
  }
  .billboard > * { position: absolute; }
  .brand-panel { left: 0; top: 0; }
  .brand-mark {
    left: 85px; top: 14px; width: 204px; height: 220px;
    display: flex; flex-direction: column; align-items: center; justify-content: center; gap: 14px;
  }
  .brand-mark .dot { width: 120px; height: 120px; border-radius: 50%; background: var(--blue); }
  .brand-mark .mark-name {
    color: var(--blue); font-weight: 700; font-size: 20px; text-align: center; line-height: 1.15;
  }
  .brand-name {
    left: 290px; width: 546px; top: 30px; text-align: center;
    color: var(--white); font-family: "Cinzel", serif; font-weight: 700; font-size: 40px; line-height: 1;
  }
  .brand-sub {
    left: 300px; width: 526px; top: 88px;
    display: flex; align-items: center; gap: 14px;
    color: var(--blue); font-family: "Cinzel", serif; font-weight: 500; font-size: 30px; letter-spacing: 12px;
  }
  .brand-sub::before, .brand-sub::after { content: ""; flex: 1; height: 3px; background: var(--blue); }
  .brand-sub span { margin-right: -12px; }
  .tagline {
    left: 290px; width: 546px; top: 138px; text-align: center;
    color: var(--white); font-family: "Cinzel", serif; font-weight: 700; font-size: 30px; letter-spacing: -0.5px;
  }
  .promise {
    left: 290px; width: 546px; top: 188px; text-align: center;
    color: var(--orange); font-family: "Playfair Display", serif; font-style: italic; font-weight: 900; font-size: 37px;
    letter-spacing: -0.5px;
  }
  .phone-icon { left: 22px; top: 265px; width: 67px; height: 67px; }
  .phone-number {
    left: 100px; top: 262px; color: var(--orange); font-weight: 700; font-size: 53px; letter-spacing: -2px; line-height: 1.3;
    white-space: nowrap;
  }
  .divider { left: 585px; top: 265px; width: 2px; height: 68px; background: var(--blue); }
  .award {
    left: 598px; width: 238px; top: 274px; text-align: center;
    color: var(--blue); font-weight: 700; font-size: 19px; line-height: 1.2;
  }
  .ratings { left: 880px; width: 218px; top: 0; height: 337px; text-align: center; }
  .ratings > * { position: absolute; left: 0; width: 100%; }
  .rating-title { top: 14px; color: var(--red); font-weight: 600; font-size: 40px; line-height: 1.3; }
  .badge {
    top: 86px; left: 8px; width: 200px; height: 75px;
    border: 2px solid var(--badge-blue); border-radius: 8px; background: var(--white); overflow: hidden;
  }
  .badge::after { content: ""; position: absolute; right: 0; top: 0; width: 66%; height: 100%; background: var(--badge-blue); }
  .badge-caption { top: 163px; color: var(--badge-blue); font-weight: 700; font-size: 14px; }
  .review-name { top: 195px; color: var(--blue); font-weight: 600; font-size: 42px; line-height: 1.3; }
  .stars { top: 250px; color: var(--star); font-size: 22px; letter-spacing: 1px; line-height: 1; }
  .community-name { top: 283px; color: var(--green); font-weight: 700; font-size: 32px; line-height: 1.3; }
</style>
</head>
<body>
  <div class="billboard">
    <svg class="brand-panel" width="1110" height="337" viewBox="0 0 1110 337" aria-hidden="true">
      <polygon points="0,0 888,0 821,254 0,254" fill="var(--ink)"/>
    </svg>

    <div class="brand-mark">
      <div class="dot"></div>
      <div class="mark-name">Claim Keeper's<br>Group</div>
    </div>

    <h1 class="brand-name">THE CLAIM KEEPER'S</h1>
    <div class="brand-sub"><span>GROUP</span></div>
    <p class="tagline">EXPERT PUBLIC ADJUSTERS</p>
    <p class="promise">"MAXIMIZED SETTLEMENT"</p>

    <svg class="phone-icon" viewBox="0 0 68 68" aria-hidden="true">
      <circle cx="34" cy="34" r="34" fill="var(--blue)"/>
      <path d="M22 17c2-1.5 4-1 5 1l4 7c1 2 .5 3.5-1 4.5l-2 1.5c1.5 4 4.5 7.5 8.5 9.5l1.7-2c1.2-1.4 3-1.7 4.5-.7l6.5 4.2c1.8 1.2 2 3.3.6 5l-2.3 2.7c-2 2.3-5.5 3-9 1.5C28 47 20 38 17.5 27.5c-.8-3.6.4-7.7 2.5-9.2z" fill="var(--white)"/>
    </svg>
    <p class="phone-number">855-FAIR DEAL</p>
    <div class="divider"></div>
    <p class="award">Voted 2022 BEST<br>Local Public Adjuster</p>

    <div class="ratings">
      <p class="rating-title">A+ Rating</p>
      <div class="badge" role="img" aria-label="Accreditation badge"></div>
      <p class="badge-caption">QRS Rating: A+</p>
      <p class="review-name">Zorbix</p>
      <p class="stars" aria-label="Five stars">★★★★★</p>
      <p class="community-name">PORCHLINE</p>
    </div>
  </div>
</body>
</html>
```